Corvane Lending Partners. Professional and Established Company

A full service finance company specializing in obtaining capital for small business. Business Lending advisor, helping small business owners access the capital they need to launch, grow, or sustain their business. Many of our programs offer flexible guidelines to overcome common obstacles such as credit score, credit history, and time in business, financials, and industry type. Our streamlined funding process makes getting a business loan, business line of credit, stated income commercial real estate loan, a smooth and stress free experience.SOME OF THE MOST COMMON NEEDS FOR BUSINESS CAPITAL:• Working Capital• Debt Consolidations (loans, merchant cash advances, etc.)• Payroll• Operating Expenses• Inventory• Equipment Financing• Commercial Real Estate (Purchase, Fix & Flip, Rehab, Renovations)• Business Acquisitions• Business ExpansionWe like the websites:www.quillmorecf.com they are in the same industry and provide the same servicesWe are wanting to be able to update when we do press releases and such using Word Press. Our look should be very professional and we will be adding Our Team Professional Bios and Headshots.

Industry/Entity Type

Finance

Number of Pages Required

5+ page

Font styles to use
Serif
Sans Serif

Requirements
Must have
• We want to copy quillmorecf.com
• We need:
• Home Page
• About Us
• Loan Programs
• Loan Criteria
• News
• Apply Now
• Contact
Nice to have
• See quillmorecf.com
Should not have
• Need professional design. Nothing bright or abstract

```html
<!DOCTYPE html>
<html lang="en">
<head>
<meta charset="utf-8">
<title>Corvane Lending Partners</title>
<link rel="stylesheet" href="https://fonts.googleapis.com/css2?family=Libre+Baskerville&family=Oswald:wght@500&family=Open+Sans:wght@400;600&display=swap">
<style>
:root{
  --blue:#1d5db4;
  --blue-dark:#0f3f8c;
  --ink:#222;
  --muted:#444;
  --panel:#efefef;
  --footer:#0b0b0b;
  --white:#fff;
}
*{box-sizing:border-box;margin:0;padding:0}
html,body{width:1200px;height:4663px;overflow:hidden}
body{position:relative;background:var(--white);font-family:"Open Sans",Arial,sans-serif;color:var(--ink)}
.abs{position:absolute}

/* header */
.brand{left:93px;top:38px;color:var(--blue);font-family:"Libre Baskerville",Georgia,serif;text-align:center}
.brand .name{font-size:44px;letter-spacing:3px;line-height:1}
.brand .sub{font-size:14px;letter-spacing:4px;margin-top:6px}
.contact-top{left:790px;top:36px;display:flex;align-items:center;gap:8px;font-size:20px;color:#333}
.social-top{left:995px;top:38px;display:flex;gap:9px}
.social-top span{width:20px;height:20px;background:#222;border-radius:3px}
.nav{left:392px;top:92px;display:flex;gap:29px;font-size:15px;color:#222;font-family:"Libre Baskerville",Georgia,serif}
.nav .active{color:var(--blue)}

/* hero */
.hero{left:0;top:162px;width:1200px;height:590px;background:linear-gradient(100deg,#8f9496 0%,#b4b7b6 40%,#a4a7a9 70%,#6f7378 100%)}
.hero-shade{left:0;top:162px;width:1200px;height:590px;background:rgba(0,0,0,.18)}
.hero-title{left:0;width:1200px;top:400px;text-align:center;font-family:"Oswald",Impact,sans-serif;font-weight:500;font-size:56px;color:var(--white);letter-spacing:1px;text-shadow:0 2px 6px rgba(0,0,0,.45)}
.hero-sub{left:0;width:1200px;top:470px;text-align:center;font-size:32px;line-height:46px;color:var(--white);text-shadow:0 2px 6px rgba(0,0,0,.55)}

/* split rows */
.photo-about{left:0;top:752px;width:597px;height:414px;background:linear-gradient(135deg,#5d6f86,#1d2838 60%,#8e9aa8)}
.about-panel{left:597px;top:752px;width:603px;height:414px;background:var(--panel)}
.loan-panel{left:0;top:1166px;width:597px;height:413px;background:var(--panel)}
.photo-loan{left:597px;top:1166px;width:603px;height:413px;background:linear-gradient(120deg,#b7bfc7,#3a4656 50%,#cfd3d6)}
.split-title{font-family:"Libre Baskerville",Georgia,serif;font-weight:400;font-size:40px;color:#1b1b1b;line-height:1}
.split-text{font-size:14px;line-height:29px;color:var(--muted)}
.btn{display:inline-block;background:var(--blue);color:var(--white);font-size:14px;text-align:center;border-radius:3px;line-height:34px}

/* services */
.section-title{left:0;width:1200px;text-align:center;font-family:"Libre Baskerville",Georgia,serif;font-weight:400;font-size:42px;color:#1b1b1b}
.service{width:320px;text-align:center}
.service .img{width:320px;height:218px}
.service h3{font-family:"Libre Baskerville",Georgia,serif;font-weight:400;font-size:18px;margin-top:18px;color:#1b1b1b}
.service p{font-size:13px;line-height:17px;color:var(--muted);margin-top:10px;padding:0 40px}

/* team */
.team{left:0;top:3016px;width:1200px;height:507px;background:linear-gradient(90deg,#174d9e,#1b5bb5 50%,#0f3f8c)}
.team-photo{left:155px;top:3121px;width:300px;height:300px;border-radius:50%;border:8px solid var(--white);background:linear-gradient(160deg,#aeb6bf,#38414d 70%)}
.team-title{left:519px;top:3130px;font-family:"Libre Baskerville",Georgia,serif;font-weight:400;font-size:40px;color:var(--white)}
.team-text{left:519px;top:3196px;width:580px;font-size:14px;line-height:29px;color:var(--white)}
.team-btn{left:519px;top:3360px;width:134px;background:#4a90e2}

/* news */
.news{width:314px}
.news .img{width:314px;height:212px;box-shadow:0 2px 6px rgba(0,0,0,.3)}
.news .date{font-size:13px;color:var(--blue);margin-top:36px}
.news h3{font-family:"Libre Baskerville",Georgia,serif;font-weight:400;font-size:19px;color:var(--blue-dark);margin-top:6px}
.news p{font-size:13px;line-height:22px;color:var(--muted);margin-top:8px}

/* footer */
.footer{left:0;top:4235px;width:1200px;height:428px;background:var(--footer)}
.f-head{font-family:"Libre Baskerville",Georgia,serif;font-weight:400;font-size:16px;color:var(--white);letter-spacing:.5px}
.f-contact{color:var(--white)}
.f-row{display:flex;gap:22px;align-items:flex-start;font-size:13px;line-height:22px;color:var(--white)}
.f-list{list-style:disc;font-size:13px;line-height:25px;padding-left:18px;color:var(--white)}
.f-follow{color:var(--white)}
.f-social{display:flex;align-items:center;gap:10px;font-size:14px;margin-bottom:18px;color:var(--white)}
.f-social span{width:26px;height:26px;border:1.5px solid var(--white);border-radius:50%}
.field{width:273px;height:35px;background:var(--white);color:#444;font-size:13px;padding:8px 10px}
.send{width:121px;height:34px;background:var(--blue);color:var(--white);font-size:15px;text-align:center;line-height:34px}
.copyright{left:0;width:1200px;top:4596px;text-align:center;font-size:13px;color:#ddd}
</style>
</head>
<body>

<header>
  <div class="abs brand"><div class="name">CORVANE</div><div class="sub">LENDING PARTNERS</div></div>
  <div class="abs contact-top">
    <svg width="24" height="24" viewBox="0 0 24 24"><path d="M6.6 10.8c1.4 2.8 3.8 5.1 6.6 6.6l2.2-2.2c.3-.3.7-.4 1-.2 1.1.4 2.3.6 3.6.6.6 0 1 .4 1 1V20c0 .6-.4 1-1 1C10.6 21 3 13.4 3 4c0-.6.4-1 1-1h3.5c.6 0 1 .4 1 1 0 1.3.2 2.5.6 3.6.1.3 0 .7-.2 1z" fill="var(--blue)"/></svg>
    0333 555 0142
  </div>
  <div class="abs social-top"><span></span><span></span><span></span><span></span></div>
  <nav class="abs nav"><span class="active">Home</span><span>About Us</span><span>Loan Programs</span><span>Loan Criteria</span><span>News</span><span>Apply Now</span><span>Contact</span></nav>
</header>

<section>
  <div class="abs hero" role="img" aria-label="Businesswoman working at a laptop in a bright office"></div>
  <div class="abs hero-shade"></div>
  <h1 class="abs hero-title">CORVANE LENDING PARTNERS</h1>
  <p class="abs hero-sub">Finance company specializing in<br>obtaining capital for small business</p>
</section>

<section>
  <div class="abs photo-about" role="img" aria-label="Hands using a phone beside a laptop showing charts"></div>
  <div class="abs about-panel">
    <h2 class="split-title" style="position:absolute;left:56px;top:72px">About Us</h2>
    <p class="split-text" style="position:absolute;left:56px;top:124px;width:500px">It is a long established fact that a reader will be distracted by the readable content of a page when looking at its layout. The point of using Lorem Ipsum is that it has a more-or-less normal distribution of letters, as opposed to using 'Content here, content here', making it look like readable English. Many desktop publishing packages and web page editors now use Lorem Ipsum as their default</p>
    <span class="btn" style="position:absolute;left:56px;top:318px;width:130px">Read More</span>
  </div>
  <div class="abs loan-panel">
    <h2 class="split-title" style="position:absolute;left:93px;top:100px">Loan Programs</h2>
    <p class="split-text" style="position:absolute;left:93px;top:152px;width:470px">It is a long established fact that a reader will be distracted by the readable content of a page when looking at its layout. The point of using Lorem Ipsum is that it has a more-or-less normal distribution of letters, as opposed to using 'Content here, content here', making it look like readable English. Many desktop publishing packages and web page editors now use Lorem Ipsum as their default</p>
    <span class="btn" style="position:absolute;left:93px;top:348px;width:131px">Read More</span>
  </div>
  <div class="abs photo-loan" role="img" aria-label="Two businessmen in suits discussing documents at a desk"></div>
</section>

<section>
  <h2 class="abs section-title" style="top:1712px">Our Services</h2>
  <div class="abs service" style="left:93px;top:1825px"><div class="img" role="img" aria-label="Hands reviewing financial charts on paper" style="background:linear-gradient(135deg,#d8c6a8,#8a7560)"></div><h3>Working Capital</h3><p>Neque porro quisquam est qui dolorem ipsum quia dolor sit amet</p></div>
  <div class="abs service" style="left:441px;top:1825px"><div class="img" role="img" aria-label="Debt consolidation note on a desk with calculator" style="background:linear-gradient(135deg,#e8e2d2,#9a9384)"></div><h3>Debt Consolidations</h3><p>Neque porro quisquam est qui dolorem ipsum quia dolor sit amet</p></div>
  <div class="abs service" style="left:790px;top:1825px"><div class="img" role="img" aria-label="Hands using a calculator over payroll papers" style="background:linear-gradient(135deg,#c9c6c0,#4e4a46)"></div><h3>Payroll</h3><p>Neque porro quisquam est qui dolorem ipsum quia dolor sit amet</p></div>

  <div class="abs service" style="left:93px;top:2207px"><div class="img" role="img" aria-label="Jar of coins with a plant beside an operating expenses card" style="background:linear-gradient(135deg,#2a2a2a,#0c0c0c 60%,#6c6c6c)"></div><h3>Operating Expenses</h3><p>Neque porro quisquam est qui dolorem ipsum quia dolor sit amet</p></div>
  <div class="abs service" style="left:441px;top:2207px"><div class="img" role="img" aria-label="Person holding a tablet in a warehouse" style="background:linear-gradient(135deg,#7b7670,#2c2a28)"></div><h3>Inventory</h3><p>Neque porro quisquam est qui dolorem ipsum quia dolor sit amet</p></div>
  <div class="abs service" style="left:790px;top:2207px"><div class="img" role="img" aria-label="Laptop keyboard with a finance key" style="background:linear-gradient(135deg,#4a4d52,#16181b 60%,#8a8e94)"></div><h3>Equipment Financing</h3><p>Neque porro quisquam est qui dolorem ipsum quia dolor sit amet</p></div>

  <div class="abs service" style="left:93px;top:2581px"><div class="img" role="img" aria-label="Modern glass office building under a blue sky" style="background:linear-gradient(180deg,#7fa6d6,#3d5e86 60%,#6d8a5a)"></div><h3>Commercial Real Estate</h3><p>Neque porro quisquam est qui dolorem ipsum quia dolor sit amet</p></div>
  <div class="abs service" style="left:441px;top:2581px"><div class="img" role="img" aria-label="Business people reviewing papers around a table" style="background:linear-gradient(135deg,#e2ddd4,#6b6257)"></div><h3>Business Acquisitions</h3><p>Neque porro quisquam est qui dolorem ipsum quia dolor sit amet</p></div>
  <div class="abs service" style="left:790px;top:2581px"><div class="img" role="img" aria-label="Growth chart on paper with a pen" style="background:linear-gradient(135deg,#dcdfe0,#7c8588)"></div><h3>Business Expansion</h3><p>Neque porro quisquam est qui dolorem ipsum quia dolor sit amet</p></div>
</section>

<section>
  <div class="abs team"></div>
  <div class="abs team-photo" role="img" aria-label="Headshot of a team member in a suit"></div>
  <h2 class="abs team-title">Our Team</h2>
  <p class="abs team-text">It is a long established fact that a reader will be distracted by the readable content of a page when looking at its layout. The point of using Lorem Ipsum is that it has a more-or-less normal distribution of letters, as opposed to using 'Content here, content here', making it look like readable English. Many desktop publishing packages and web page editors now use Lorem Ipsum as their default model text.</p>
  <span class="abs btn team-btn">View More</span>
</section>

<section>
  <h2 class="abs section-title" style="top:3652px">Latest News</h2>
  <article class="abs news" style="left:90px;top:3765px"><div class="img" role="img" aria-label="Team meeting around a conference table" style="background:linear-gradient(135deg,#8b8c8e,#2e3034)"></div><div class="date">July 12,2018</div><h3>Neque porro quisquam</h3><p>It is a long established fact that a reader will be distracted by the readable content</p></article>
  <article class="abs news" style="left:435px;top:3765px"><div class="img" role="img" aria-label="Stacks of coins in front of a city skyline" style="background:linear-gradient(135deg,#4f6a8c,#1b2536 60%,#a08a5c)"></div><div class="date">July 12,2018</div><h3>Dolorem ipsum quia</h3><p>It is a long established fact that a reader will be distracted by the readable content</p></article>
  <article class="abs news" style="left:780px;top:3765px"><div class="img" role="img" aria-label="Hands working on documents and a laptop" style="background:linear-gradient(135deg,#d6d4d0,#5e5a56)"></div><div class="date">July 12,2018</div><h3>Porro quisquam est qui</h3><p>It is a long established fact that a reader will be distracted by the readable content</p></article>
</section>

<footer>
  <div class="abs footer"></div>
  <h4 class="abs f-head" style="left:96px;top:4312px">CONTACT US</h4>
  <div class="abs f-contact" style="left:96px;top:4368px">
    <div class="f-row"><svg width="14" height="18" viewBox="0 0 14 18"><path d="M7 0C3.1 0 0 3.1 0 7c0 5 7 11 7 11s7-6 7-11c0-3.9-3.1-7-7-7zm0 9.5A2.5 2.5 0 1 1 7 4.5a2.5 2.5 0 0 1 0 5z" fill="#fff"/></svg><span>27 Alder Row, Westmere,<br>WA 6019</span></div>
    <div class="f-row" style="margin-top:18px"><svg width="14" height="14" viewBox="0 0 24 24"><path d="M6.6 10.8c1.4 2.8 3.8 5.1 6.6 6.6l2.2-2.2c.3-.3.7-.4 1-.2 1.1.4 2.3.6 3.6.6.6 0 1 .4 1 1V20c0 .6-.4 1-1 1C10.6 21 3 13.4 3 4c0-.6.4-1 1-1h3.5c.6 0 1 .4 1 1 0 1.3.2 2.5.6 3.6.1.3 0 .7-.2 1z" fill="#fff"/></svg><span>08 5550 2716</span></div>
    <div class="f-row" style="margin-top:16px"><svg width="14" height="12" viewBox="0 0 14 12"><rect width="14" height="12" rx="1" fill="#fff"/><path d="M0 1l7 5 7-5" stroke="#0b0b0b" stroke-width="1.4" fill="none"/></svg><span>hello@corvanelending.com</span></div>
  </div>
  <h4 class="abs f-head" style="left:389px;top:4312px">QUICK LINKS</h4>
  <ul class="abs f-list" style="left:393px;top:4366px"><li>Home</li><li>About us</li><li>Products</li><li>Blog</li><li>Contact Us</li></ul>
  <h4 class="abs f-head" style="left:609px;top:4312px">FOLLOW US</h4>
  <div class="abs f-follow" style="left:612px;top:4366px">
    <div class="f-social"><span></span>Socialbook</div>
    <div class="f-social"><span></span>Chirper</div>
    <div class="f-social"><span></span>Circles</div>
  </div>
  <h4 class="abs f-head" style="left:827px;top:4312px">NEWSLETTER</h4>
  <div class="abs field" style="left:827px;top:4374px">Your Name</div>
  <div class="abs field" style="left:827px;top:4418px">Email address</div>
  <div class="abs send" style="left:827px;top:4471px">SEND</div>
  <p class="abs copyright">© Copyright 2018 . All Rights Reserved.</p>
</footer>

</body>
</html>
```